Local Flower Farm Needs Business Card Design

I need business cards designed for a flower farm based in Eudora, Kansas.
Business Info:
We are a local cut flower farm located in Eudora, Kansas, founded by Corinne Haldwick. What started as a passion for agriculture and search for more joy in daily life has blossomed into a small business dedicated to providing the community with beautiful, fresh, and sustainable flowers. We specialize in local, seasonal blooms, ensuring that every petal reflects the care and dedication we pour into our craft. Our mission is to deliver the highest quality flowers directly to our customers through local farmers markets and to florists who share our commitment to sustainability. Join us in celebrating the beauty of nature, one bloom at a time!
Contact Details:
Corinne Haldwick
Owner
Phone 913-555-0147
Facebook: Rosalind Thorpe Gardens
Instagram: @RosalindThorpeGardens
Website: RosalindThorpeGardens.example
Target Market(s)
Wholesale to Florists and Direct to Consumer via Farmers Market
Industry/Entity Type
Florist, Farm
Contact Information for Business Card
Name, Contact Info, Logo
Look and feel
Each slider illustrates characteristics of the customer's brand and the style your logo design should communicate.

```html
<!DOCTYPE html>
<html lang="en">
<head>
<meta charset="utf-8">
<title>Rosalind Thorpe Gardens – Business Card</title>
<link rel="stylesheet" href="https://fonts.googleapis.com/css2?family=Lora:wght@400;700&display=swap">
<style>
  :root {
    --forest: #0d2a2e;
    --paper: #ffffff;
    --ink: #12302f;
    --muted: #5c6668;
    --sage-faint: rgba(170, 196, 196, 0.22);
    --grey-faint: rgba(120, 130, 134, 0.18);
    --backdrop: #e9e6e1;
  }
  * { box-sizing: border-box; margin: 0; padding: 0; }
  html, body {
    width: 1200px; height: 900px; overflow: hidden;
    background: var(--backdrop);
    font-family: "Lora", Georgia, serif;
  }
  .sheet {
    width: 1200px; height: 900px;
    display: flex; flex-direction: column; align-items: center; justify-content: center;
    gap: 40px;
  }
  .card {
    position: relative;
    width: 700px; height: 400px;
    overflow: hidden;
    box-shadow: 0 6px 18px rgba(0,0,0,0.12);
  }
  .card--front { background: var(--forest); }
  .card--back { background: var(--paper); }

  .floral-band {
    position: absolute;
    left: 150px; right: 0; bottom: 0; height: 200px;
    clip-path: polygon(0 100%, 30% 55%, 60% 30%, 100% 0, 100% 100%);
  }
  .card--front .floral-band {
    background: linear-gradient(20deg, transparent 10%, var(--sage-faint) 60%);
  }
  .card--back .floral-band {
    background: linear-gradient(20deg, transparent 10%, var(--grey-faint) 60%);
  }

  .brand {
    position: absolute;
    display: flex; align-items: center; gap: 12px;
  }
  .brand__dot {
    width: 22px; height: 22px; border-radius: 50%;
    border: 1.5px solid currentColor;
    flex: none;
  }
  .brand__name {
    font-size: 22px; font-weight: 400; letter-spacing: 0.14em;
    text-transform: uppercase; line-height: 1.3;
  }
  .card--front .brand { color: var(--paper); left: 190px; top: 110px; }
  .card--back .brand { color: var(--ink); left: 46px; top: 150px; width: 260px; }
  .card--back .brand__name { font-size: 20px; }

  .contact {
    position: absolute; left: 330px; top: 70px;
    color: var(--ink);
  }
  .contact__name {
    font-size: 24px; font-weight: 700; letter-spacing: 0.04em; text-transform: uppercase;
  }
  .contact__role {
    font-size: 17px; color: var(--muted); margin: 2px 0 18px 22px;
  }
  .contact__list { list-style: none; margin-left: 40px; }
  .contact__item {
    display: flex; align-items: center; gap: 10px;
    font-size: 19px; line-height: 30px; color: var(--ink);
  }
  .contact__icon { width: 16px; height: 16px; flex: none; }
  .contact__bullet {
    width: 14px; height: 14px; border-radius: 50%; background: var(--ink); flex: none; margin: 0 1px;
  }
</style>
</head>
<body>
<main class="sheet">
  <section class="card card--front" aria-label="Card front">
    <div class="floral-band" role="img" aria-label="Faint line-drawn wildflowers rising along the lower edge"></div>
    <div class="brand">
      <span class="brand__dot"></span>
      <span class="brand__name">Rosalind Thorpe Gardens</span>
    </div>
  </section>

  <section class="card card--back" aria-label="Card back">
    <div class="floral-band" role="img" aria-label="Faint grey line-drawn wildflowers along the lower edge"></div>
    <div class="brand">
      <span class="brand__dot"></span>
      <span class="brand__name">Rosalind Thorpe Gardens</span>
    </div>
    <div class="contact">
      <p class="contact__name">Corinne Haldwick</p>
      <p class="contact__role">Owner</p>
      <ul class="contact__list">
        <li class="contact__item">
          <svg class="contact__icon" viewBox="0 0 16 16" aria-hidden="true"><path d="M3 1.5l2.5 0 1.2 3-1.6 1.2a8 8 0 0 0 5.2 5.2l1.2-1.6 3 1.2v2.5a1.5 1.5 0 0 1-1.6 1.5A12.5 12.5 0 0 1 1.5 3.1 1.5 1.5 0 0 1 3 1.5z" fill="var(--ink)"/></svg>
          913-555-0147
        </li>
        <li class="contact__item"><span class="contact__bullet"></span>Rosalind Thorpe Gardens</li>
        <li class="contact__item"><span class="contact__bullet"></span>@RosalindThorpeGardens</li>
        <li class="contact__item">
          <svg class="contact__icon" viewBox="0 0 16 16" aria-hidden="true" fill="none" stroke="var(--ink)" stroke-width="1.3"><circle cx="8" cy="8" r="6.5"/><ellipse cx="8" cy="8" rx="3" ry="6.5"/><path d="M1.5 8h13M2.5 4.8h11M2.5 11.2h11"/></svg>
          RosalindThorpeGardens.example
        </li>
      </ul>
    </div>
  </section>
</main>
</body>
</html>
```